Maple Gable Business Card

Colors can be blue, grey and white as you see in the attached logo. Needs to have a spot for name, title, phone, email, address, and website. There also needs to be a spot for an agent's picture.

Contact Information for Business Card

See project description.

Colors

Designer to choose colors to be used in the design.

```html
<!DOCTYPE html>
<html lang="en">
<head>
<meta charset="utf-8">
<title>Maple Gable Business Card</title>
<link rel="stylesheet" href="https://fonts.googleapis.com/css2?family=Roboto:wght@400;500;700&display=swap">
<style>
  :root {
    --page-bg: #e6e7ea;
    --card-white: #ffffff;
    --brand-blue: #2a77b8;
    --text-blue: #2b6fb3;
    --text-grey: #555a60;
    --rule-grey: #8a8d91;
    --photo-top: #d9e3ee;
    --photo-bottom: #b9c9db;
    --shadow: rgba(0, 0, 0, 0.18);
  }
  * { box-sizing: border-box; margin: 0; padding: 0; }
  html, body {
    width: 1200px; height: 1108px; overflow: hidden;
    background: var(--page-bg);
    font-family: "Roboto", Arial, sans-serif;
  }
  .stage {
    position: relative; width: 1200px; height: 1108px;
    display: flex; justify-content: center; align-items: center; gap: 70px;
  }
  .card {
    width: 410px; height: 700px; border-radius: 30px;
    box-shadow: 0 14px 34px var(--shadow);
    display: flex; flex-direction: column; align-items: center;
    position: relative;
  }
  .card--front { background: var(--card-white); padding-top: 100px; }
  .card--back { background: var(--brand-blue); justify-content: center; }

  .brand {
    display: flex; align-items: center; gap: 12px;
    font-family: "Roboto", Arial, sans-serif; font-weight: 700;
    font-size: 38px; letter-spacing: 0.5px; text-transform: uppercase;
    line-height: 1.1;
  }
  .brand__mark { width: 22px; height: 22px; }
  .card--front .brand { color: var(--text-blue); }
  .card--front .brand__mark { background: var(--text-blue); }
  .card--back .brand { color: var(--card-white); }
  .card--back .brand__mark { background: var(--card-white); }

  .agent-photo {
    width: 120px; height: 120px; border-radius: 50%;
    margin-top: 36px;
    background: linear-gradient(180deg, var(--photo-top), var(--photo-bottom));
    border: 3px solid var(--text-blue);
  }

  .person { margin-top: 24px; text-align: center; }
  .person__name { color: var(--text-blue); font-weight: 700; font-size: 30px; line-height: 1.15; }
  .person__title { color: var(--text-grey); font-size: 22px; margin-top: 2px; }

  .divider {
    width: 230px; margin-top: 10px;
    display: flex; align-items: center; gap: 6px;
  }
  .divider__line { flex: 1; height: 1.5px; background: var(--rule-grey); }
  .icon { width: 24px; height: 24px; }

  .contact {
    margin-top: 12px; text-align: center;
    color: var(--text-grey); font-size: 22px; line-height: 1.28;
  }
  .contact__site-name { color: var(--text-blue); }

  .rule { width: 230px; height: 1.5px; background: var(--rule-grey); margin-top: 12px; }

  .address {
    margin-top: 12px; text-align: center;
    color: var(--text-grey); font-size: 22px; line-height: 1.3;
  }
</style>
</head>
<body>
<main class="stage">
  <section class="card card--front" aria-label="Card front">
    <div class="brand"><span class="brand__mark"></span>Maple Gable</div>

    <div class="agent-photo" role="img" aria-label="Agent portrait photo"></div>

    <div class="person">
      <p class="person__name">Daniel Reyes</p>
      <p class="person__title">Manager</p>
    </div>

    <div class="divider">
      <span class="divider__line"></span>
      <svg class="icon" viewBox="0 0 24 24" aria-label="Phone">
        <circle cx="12" cy="12" r="12" fill="#2b6fb3"/>
        <path d="M8 7.5c.6-.6 1.4-.5 1.7.2l.9 1.8c.2.5 0 1-.4 1.3l-.6.4c.6 1.4 1.7 2.5 3.1 3.1l.4-.6c.3-.4.8-.6 1.3-.4l1.8.9c.7.3.8 1.1.2 1.7l-.9.9c-.6.6-1.6.7-2.4.3-2.5-1.2-4.500-3.2-5.7-5.700-.4-.8-.3-1.8.3-2.4z" fill="#fff"/>
      </svg>
      <svg class="icon" viewBox="0 0 24 24" aria-label="Email">
        <circle cx="12" cy="12" r="12" fill="#2b6fb3"/>
        <rect x="6" y="8" width="12" height="8.5" rx="1" fill="#fff"/>
        <path d="M6.5 8.5 12 13l5.5-4.5" fill="none" stroke="#2b6fb3" stroke-width="1.2"/>
      </svg>
      <svg class="icon" viewBox="0 0 24 24" aria-label="Website">
        <circle cx="12" cy="12" r="12" fill="#2b6fb3"/>
        <circle cx="12" cy="12" r="6" fill="none" stroke="#fff" stroke-width="1.4"/>
        <ellipse cx="12" cy="12" rx="2.6" ry="6" fill="none" stroke="#fff" stroke-width="1.2"/>
        <path d="M6 12h12" stroke="#fff" stroke-width="1.2"/>
      </svg>
      <span class="divider__line"></span>
    </div>

    <div class="contact">
      <p>555-014-2100</p>
      <p>youremail@mailbox.com</p>
      <p>www.<span class="contact__site-name">yourwebsite</span>.com</p>
    </div>

    <div class="rule"></div>

    <div class="address">
      <p>Your address, city</p>
      <p>state, ZIP 0000</p>
    </div>
  </section>

  <section class="card card--back" aria-label="Card back">
    <div class="brand"><span class="brand__mark"></span>Maple Gable</div>
  </section>
</main>
</body>
</html>
```